Brindle Healthcare Coming Soon Sign

I need a large (10 x5) road banner announcing the construction of our new medical practice at 5187 Larkmoor Road in John's Island. The name of our practice is Brindle Healthcare and we thought it would be fund to nick name it the "Brindle Waystation". We'd like the tagline to read - "There's nothing healthy about driving an hour to see your doctor. So we're coming to you." Opening Late 2025 I have attached three logos as we have two other practices (Brindle Urgent and Brindle Aesthetics ) that should be present on the bottom of the sign but the main business is Brindle Healthcare. For more information on our look/feel visit our website www.goplainway-example.com (which should be somewhere on the banner as well)
Updates

The signage needs to say Coming Late Fall 2025!

Target Market(s)

Drive By traffic must be made aware that we are coming soon

Industry/Entity Type

Healthcare

Requirements
Nice to have
• Western Theme

```html
<!DOCTYPE html>
<html lang="en">
<head>
<meta charset="utf-8">
<title>Brindle Healthcare – Coming Late Fall 2025</title>
<link href="https://fonts.googleapis.com/css2?family=Montserrat:wght@700;800&family=Teko:wght@600&family=Oswald:wght@500;600&display=swap" rel="stylesheet">
<style>
  :root {
    --stage: #343434;
    --frame: #6b8496;
    --paper: #f2f2f1;
    --paper-shade: #dadcdd;
    --navy: #15294d;
    --sky: #3a8fcb;
    --sky-light: #5aa7de;
    --red: #ef4536;
    --pink: #e3197d;
  }
  * { margin: 0; padding: 0; box-sizing: border-box; }
  html, body { width: 1200px; height: 738px; overflow: hidden; background: var(--stage); }
  .banner {
    position: absolute; left: 120px; top: 111px; width: 997px; height: 498px;
    background: var(--frame);
  }
  .banner__paper {
    position: absolute; inset: 12px 12px 14px 12px;
    background: radial-gradient(ellipse at 72% 52%, #ffffff 0%, var(--paper) 45%, var(--paper-shade) 100%);
  }
  .scene {
    position: absolute; left: 528px; top: 133px; width: 356px; height: 260px;
    background: linear-gradient(180deg, #2a3f63 0%, #1b2f55 60%, #15294d 100%);
    border-radius: 178px 178px 6px 6px;
  }
  .artwork { position: absolute; inset: 0; }
  .t-display { font-family: "Teko", sans-serif; font-weight: 600; }
  .t-brand { font-family: "Montserrat", sans-serif; font-weight: 800; }
  .t-announce { font-family: "Oswald", sans-serif; font-weight: 600; font-size: 46px; fill: var(--red); }
  .t-site { font-family: "Oswald", sans-serif; font-weight: 500; font-size: 34px; fill: var(--navy); }
  .navy { fill: var(--navy); }
  .sky { fill: var(--sky); }
  .sky-light { fill: var(--sky-light); }
  .white { fill: #ffffff; }
  .pink { fill: var(--pink); }
  .red { fill: var(--red); }
</style>
</head>
<body>
  <main class="banner">
    <div class="banner__paper"></div>

    <div class="scene" role="img" aria-label="Navy silhouette of campers on a lakeside dock with pine trees, a tent, a flag, birds and a helicopter against a rising sun"></div>

    <svg class="artwork" width="997" height="498" viewBox="0 0 997 498">
      <g class="brand">
        <rect class="navy" x="124" y="55" width="54" height="54"/>
        <text class="t-brand navy" x="204" y="81" font-size="37" textLength="184" lengthAdjust="spacingAndGlyphs">BRINDLE</text>
        <text class="t-brand navy" x="203" y="109" font-size="23" textLength="182" lengthAdjust="spacingAndGlyphs">HEALTHCARE</text>
      </g>

      <g class="headline">
        <text class="t-display navy" x="86" y="205" font-size="88" textLength="376" lengthAdjust="spacingAndGlyphs">CONSERVING RURAL</text>
        <path class="sky" d="M86 205 Q275 186 464 205 L464 271 L86 271 Z"/>
        <text class="t-display white" x="94" y="265" font-size="76" textLength="362" lengthAdjust="spacingAndGlyphs">JOHN'S ISLAND</text>
        <rect class="navy" x="90" y="285" width="146" height="3"/>
        <rect class="navy" x="314" y="285" width="146" height="3"/>
        <text class="t-display sky" x="275" y="297" font-size="32" text-anchor="middle" textLength="68" lengthAdjust="spacingAndGlyphs">WITH</text>
        <text class="t-display sky-light" x="86" y="333" font-size="44" textLength="376" lengthAdjust="spacingAndGlyphs">HOME GROWN PROGRESSIVE</text>
        <text class="t-brand navy" x="133" y="367" font-size="40" textLength="285" lengthAdjust="spacingAndGlyphs">PRIMARY CARE</text>
      </g>

      <g class="practice practice--aesthetics">
        <circle class="pink" cx="115" cy="415" r="22"/>
        <text class="t-brand pink" x="158" y="417" font-size="26" textLength="106" lengthAdjust="spacingAndGlyphs">BRINDLE</text>
        <text class="t-brand pink" x="160" y="434" font-size="15" textLength="101" lengthAdjust="spacingAndGlyphs">AESTHETICS</text>
      </g>
      <g class="practice practice--urgent">
        <rect class="red" x="296" y="396" width="40" height="40"/>
        <text class="t-brand red" x="360" y="417" font-size="26" textLength="98" lengthAdjust="spacingAndGlyphs">BRINDLE</text>
        <text class="t-brand red" x="361" y="434" font-size="15" textLength="96" lengthAdjust="spacingAndGlyphs">URGENT</text>
      </g>

      <defs>
        <path id="announceArc" d="M454 355 A254 254 0 0 1 962 355"/>
      </defs>
      <text class="t-announce"><textPath href="#announceArc" startOffset="50%" text-anchor="middle" textLength="520" lengthAdjust="spacing">COMING LATE FALL 2025!</textPath></text>

      <text class="t-site" x="514" y="433" textLength="372" lengthAdjust="spacingAndGlyphs">BRINDLEHEALTHCARE-EXAMPLE.COM</text>
    </svg>
  </main>
</body>
</html>
```